SEO and image area for top of invitation website

We need to add an area on our final category pages for SEO text. Instead of just adding text, we'd like to develop a graphical approach that keeps with our soft, feminine look.

You can view an example of our current final category page at http://www.cardwrenpress.example/invitations/boy-birthday

I've attached an image of what we're thinking it could look like, but you're welcome to alter the design.

The area should be the same width as our site, but can be any height you determine appropriate.

The winner of this project may be approached to develop the additional designs and backgrounds for us as another project. We additionally have several other projects we're interested in doing with the winner.
Updates

We have had a question about the right side of the banner, and what "Free Unlimited Proofs" mean.

About Free Unlimited Proofs:

We are a custom invitation printing company. When a customer orders an invitation from us, they tell us what information we want on the invitation. We then create an electronic sample, or "proof", of what it will look like. We then email it to the customer and they can tell us if they want to make any more changes. We will continue to send them samples, or what we call "proofs", until they are completely satisfied with the way it looks.

We offer Free UNLIMITED Proofs. Compared to our competitors, we are the only one to offer free unlimited proofs.

So, for the right side of this banner, we need an image, or a badge, promoting that we offer free unlimited proofs, and you can include that we are the only ones to do it, if your design has space for that information.

Also, keep in mind, that for other category pages, we may create different images or badges to put in this area - such as for our Low Price Guarantee or to promote a coupon or specific product, for example. So, your design should be able to work with various images on the right side.

Target Market(s)

Our demographic is 100% women, ages 25-60.

Industry/Entity Type

Seo

Requirements
Must have
• The area must have 3 things:
1) Area for the title of the page.
2) Area for SEO text describing the category page.
3) Area for an image. Keep in mind that this image may change for each category page. For this project, you will create an image for our offering of "Free Unlimited Proofs". On other pages, we may display other images we create such as "Low Price Guarantee" or images of certain products we'd like to promote. Just keep this in mind when you're making the design flow.
Nice to have
• Optional: Light design background. We wouldn't mind there being a slight graphical background to this area, to keep it interesting to the eye. Then, for other category pages, we may make additional backgrounds to use in this box area.

```html
<!DOCTYPE html>
<html lang="en">
<head>
<meta charset="utf-8">
<title>Boy Birthday Invitations · Card Wren Press</title>
<link rel="stylesheet" href="https://fonts.googleapis.com/css2?family=Noto+Serif:wght@400;700&family=Open+Sans:wght@400;600;700;800&display=swap">
<style>
:root{
  --ink:#4a4a4a;
  --muted:#666;
  --brand:#6b5a5e;
  --teal:#2aa6a0;
  --line:#d8d8d8;
  --bar:#f1f1f1;
  --card:#ececec;
  --button:#fcd34d;
  --button-edge:#e3a91f;
  --coming:#d52b2b;
  --blush:#fbeef0;
  --cream:#fdf7ec;
  --rose:#c9576f;
  --rose-deep:#a8405a;
}
*{box-sizing:border-box;margin:0;padding:0}
html,body{width:1200px;height:960px;overflow:hidden;background:#fff}
body{position:relative;font-family:"Noto Serif",Georgia,serif;color:var(--ink)}
.abs{position:absolute}

.topbar{left:0;top:0;width:1200px;height:28px;background:var(--bar);border-bottom:1px solid #ddd;
  font-family:"Open Sans",Arial,sans-serif;font-size:12px;font-weight:700;color:#555;
  display:flex;align-items:center;justify-content:center}
.topbar span{padding:0 13px;border-right:1px solid #ddd;line-height:28px;display:flex;align-items:center;gap:7px}
.topbar span:last-child{border-right:none}
.topbar .phone{font-weight:600}

.brand{left:146px;top:42px;display:flex;align-items:center;gap:12px}
.brand-mark{width:60px;height:60px;background:#e4e0e1;border-radius:4px}
.brand-name{font-size:30px;color:var(--brand);letter-spacing:-.5px;white-space:nowrap}

.search{left:486px;top:63px;width:276px;height:42px;border:1px solid #e2e2e2;border-radius:4px;box-shadow:inset 0 1px 3px rgba(0,0,0,.08)}
.search-btn{position:absolute;right:6px;top:7px;width:62px;height:27px;background:#c7c7c7;border-radius:3px;
  color:#fff;font-size:12px;font-weight:700;text-align:center;line-height:27px}
.account{left:783px;top:74px;display:flex;align-items:center;gap:15px;font-size:12px;color:#555;letter-spacing:.3px}
.account .count{font-family:"Open Sans",Arial,sans-serif;font-size:15px;color:#777}

.mainnav{left:143px;top:135px;width:914px;height:45px;border-top:1px solid var(--line);border-bottom:1px solid var(--line);
  display:flex;align-items:center;gap:38px;padding-left:20px;font-size:18.5px;color:#555}

.crumbs{left:143px;top:198px;font-size:12px;color:#555}
.crumbs a{color:var(--teal);text-decoration:none}

.banner{left:141px;top:251px;width:929px;height:172px;overflow:hidden;
  background:linear-gradient(120deg,var(--cream) 0%,var(--blush) 70%)}
.banner-dots{left:0;top:0;width:929px;height:172px;
  background-image:radial-gradient(circle,rgba(201,87,111,.10) 1.6px,transparent 2px);background-size:18px 18px}
.page-title{left:30px;top:18px;font-size:26px;font-weight:400;color:var(--brand);white-space:nowrap}
.title-rule{left:32px;top:58px;width:90px;height:2px;background:var(--rose)}
.seo-text{left:32px;top:70px;width:600px;font-family:"Open Sans",Arial,sans-serif;font-size:12.5px;line-height:18px;color:var(--muted)}
.coming{left:378px;top:146px;width:164px;height:26px;background:var(--coming);color:#fff;
  font-family:"Open Sans",Arial,sans-serif;font-size:15px;line-height:26px;padding-left:13px;border-radius:10px 0 0 0}

.promo{left:680px;top:0;width:249px;height:172px;background:linear-gradient(160deg,#f6d4dc,#eab2c0)}
.badge{left:49px;top:10px;width:152px;height:152px;border-radius:50%;background:var(--rose);
  border:4px solid #fff;box-shadow:0 0 0 2px var(--rose);color:#fff;text-align:center;
  font-family:"Open Sans",Arial,sans-serif;display:flex;flex-direction:column;align-items:center;justify-content:center}
.badge .free{font-size:15px;font-weight:700;letter-spacing:2px}
.badge .big{font-size:22px;font-weight:800;line-height:24px;letter-spacing:.5px}
.badge .only{font-size:10.5px;font-weight:600;margin-top:6px;padding-top:5px;border-top:1px solid rgba(255,255,255,.6);width:104px;line-height:13px}

.sortbar{left:158px;top:432px;display:flex;align-items:baseline;gap:20px;font-size:12px;color:#555}
.sortbar .label{font-size:15px;color:#555}
.pager{left:868px;top:433px;display:flex;align-items:center;gap:9px;font-family:"Open Sans",Arial,sans-serif;font-size:12px;color:var(--teal)}
.pager .current{color:#555}
.pager svg{display:block}

.filters{left:144px;top:493px;width:228px}
.filter-title{font-size:15.5px;color:#555;display:flex;align-items:center;gap:9px;padding-left:8px}
.filter-title::before{content:"";border-left:5px solid #777;border-top:5px solid transparent;border-bottom:5px solid transparent}
.colors{list-style:none;margin:9px 0 0 25px;font-size:12px;color:#666}
.colors li{height:19px;display:flex;align-items:center;gap:7px}
.swatch{width:14px;height:14px;border-radius:50%;border:1px solid rgba(0,0,0,.12)}
.all-colors{font-family:"Open Sans",Arial,sans-serif;font-size:12px;color:#666;margin:1px 0 0 28px}
.filter-block{border-top:3px solid #ddd;height:60px;padding-top:16px}
.filter-block.first{margin-top:8px}

.card{width:211px;height:207px;background:var(--card);border:1px solid #ddd}
.art{position:absolute}
.quick{position:absolute;bottom:-13px;left:58px;width:95px;height:25px;background:var(--button);border:1px solid var(--button-edge);
  border-radius:5px;font-family:"Open Sans",Arial,sans-serif;font-size:11.5px;font-weight:700;color:#5a4a2a;text-align:center;line-height:23px}
</style>
</head>
<body>

<div class="abs topbar">
  <span><svg width="18" height="12" viewBox="0 0 18 12"><rect x="0" y="1" width="11" height="8" fill="#555"/><path d="M11 4h4l3 3v2h-7z" fill="#555"/><circle cx="4" cy="10" r="2" fill="#555"/><circle cx="14" cy="10" r="2" fill="#555"/></svg>FREE SHIPPING on orders over $150 - no coupon needed!</span>
  <span><svg width="16" height="12" viewBox="0 0 16 12"><path d="M1 1h10v6H5l-3 3V7H1z" fill="#555"/><path d="M12 4h3v5h-1v2l-2-2H7V8h5z" fill="#777"/></svg>Live Help</span>
  <span class="phone"><svg width="16" height="12" viewBox="0 0 16 12"><path d="M1 4c0-3 14-3 14 0v2h-4V4H5v2H1z" fill="#555"/><rect x="4" y="6" width="8" height="5" fill="#555"/></svg>800.555.0142</span>
  <span><svg width="14" height="14" viewBox="0 0 14 14"><path d="M1 1h6l6 6-6 6-6-6z" fill="#555"/><circle cx="4" cy="4" r="1.3" fill="#f1f1f1"/></svg>Become a Designer · Earn Commission</span>
</div>

<div class="abs brand">
  <div class="brand-mark"></div>
  <div class="brand-name">Card Wren Press</div>
</div>

<div class="abs search"><div class="search-btn">search</div></div>

<div class="abs account">
  <span>LOGIN</span><span>CREATE ACCOUNT</span>
  <svg width="20" height="16" viewBox="0 0 20 16"><path d="M0 1h4l3 9h10l2-7H5" fill="none" stroke="#666" stroke-width="2"/><circle cx="8" cy="14" r="1.6" fill="#666"/><circle cx="16" cy="14" r="1.6" fill="#666"/></svg>
  <span class="count">0</span>
</div>

<nav class="abs mainnav">
  <span>Wedding</span><span>Party</span><span>Baby and Kids</span><span>Holiday</span><span>Graduation</span><span>Business</span><span>Stationery</span>
</nav>

<div class="abs crumbs"><a href="#">Party</a> · <a href="#">Kids Birthday Party Invitations</a> · Boy Birthday Invitations</div>

<section class="abs banner">
  <div class="abs banner-dots"></div>
  <h1 class="abs page-title">Boy Birthday Invitations</h1>
  <div class="abs title-rule"></div>
  <p class="abs seo-text">Celebrate your little guy in style with birthday invitations made just for boys. Choose from pirates, dinosaurs, sports, outer space and more, then add his photo and party details. Every card is printed on premium paper, and we send you proofs until each word looks exactly right.</p>
  <div class="abs coming">Coming Soon....</div>
  <div class="abs promo">
    <div class="abs badge">
      <span class="free">FREE</span>
      <span class="big">UNLIMITED<br>PROOFS</span>
      <span class="only">The only invitation shop that offers it</span>
    </div>
  </div>
</section>

<div class="abs sortbar"><span class="label">Sort By:</span><span>Price</span><span>Name</span><span>Vendor</span></div>

<div class="abs pager">
  <svg width="21" height="21" viewBox="0 0 21 21"><circle cx="10.5" cy="10.5" r="10.5" fill="#cfcfcf"/><path d="M15 10.5H7M10 7l-3.5 3.5L10 14" stroke="#fff" stroke-width="2.2" fill="none"/></svg>
  <span class="current">1</span><span>2</span><span>3</span><span>4</span><span>5</span><span>6</span><span>7</span><span>8</span><span>9</span>
  <svg width="21" height="21" viewBox="0 0 21 21"><circle cx="10.5" cy="10.5" r="10.5" fill="var(--teal)"/><path d="M6 10.5h8M11 7l3.5 3.5L11 14" stroke="#fff" stroke-width="2.2" fill="none"/></svg>
</div>

<aside class="abs filters">
  <div class="filter-title">Filter By Color</div>
  <ul class="colors">
    <li><span class="swatch" style="background:#333"></span>Black</li>
    <li><span class="swatch" style="background:#5b8ef0"></span>Blue</li>
    <li><span class="swatch" style="background:#8a6450"></span>Brown</li>
    <li><span class="swatch" style="background:#f2b52b"></span>Gold</li>
    <li><span class="swatch" style="background:#7fd67f"></span>Green</li>
    <li><span class="swatch" style="background:#cfcfcf"></span>Grey</li>
    <li><span class="swatch" style="background:#f3f1df"></span>Ivory</li>
    <li><span class="swatch" style="background:#f5a66a"></span>Orange</li>
    <li><span class="swatch" style="background:#f8c3e8"></span>Pink</li>
    <li><span class="swatch" style="background:#7d1f6a"></span>Purple</li>
    <li><span class="swatch" style="background:#e0504a"></span>Red</li>
    <li><span class="swatch" style="background:#eef2f5"></span>Silver</li>
    <li><span class="swatch" style="background:#fff"></span>White</li>
    <li><span class="swatch" style="background:#f7ef7a"></span>Yellow</li>
  </ul>
  <div class="all-colors">ALL COLORS</div>
  <div class="filter-block first"><div class="filter-title">Filter By Card Size</div></div>
  <div class="filter-block"><div class="filter-title">Filter By # of Photos</div></div>
  <div class="filter-block"><div class="filter-title">Filter By Designer</div></div>
</aside>

<div class="abs card" style="left:391px;top:477px">
  <div class="art" style="left:30px;top:0;width:152px;height:207px;background:linear-gradient(180deg,#e8413a 0,#f3a03a 35%,#2a9fd6 70%,#7ab84a)" role="img" aria-label="Pirate party invitation with parrot, ship and photo panels"></div>
  <div class="quick">Quick View</div>
</div>
<div class="abs card" style="left:619px;top:477px">
  <div class="art" style="left:29px;top:0;width:153px;height:207px;background:linear-gradient(180deg,#7fc243 0,#7fc243 50%,#2aa2d8 52%,#2aa2d8 65%,#f5a635 66%)" role="img" aria-label="Sports birthday invitation with child photo on star pattern"></div>
  <div class="quick">Quick View</div>
</div>
<div class="abs card" style="left:846px;top:477px;background:#f2f2f2">
  <div class="art" style="left:1px;top:0;width:208px;height:130px;background:radial-gradient(ellipse at 55% 50%,#f5a623 0,#f5a623 55%,#fff 57%)" role="img" aria-label="Orange dinosaur birthday invitation"></div>
  <div class="quick">Quick View</div>
</div>

<div class="abs card" style="left:391px;top:704px">
  <div class="art" style="left:60px;top:0;width:91px;height:207px;background:linear-gradient(180deg,#3fa4e0,#6cc3f0)" role="img" aria-label="Bowling strike birthday invitation"></div>
  <div class="quick">Quick View</div>
</div>
<div class="abs card" style="left:619px;top:704px;background:#f2f2f2">
  <div class="art" style="left:2px;top:0;width:207px;height:130px;background:linear-gradient(160deg,#cde27a,#9ccd48 50%,#f2b63a 75%,#e55a3a)" role="img" aria-label="Water slide birthday party invitation"></div>
  <div class="quick">Quick View</div>
</div>
<div class="abs card" style="left:846px;top:704px;background:#f2f2f2">
  <div class="art" style="left:2px;top:0;width:206px;height:130px;background:linear-gradient(135deg,#2fa7e3,#1b8fd0)" role="img" aria-label="Space alien birthday invitation on blue sky"></div>
  <div class="quick">Quick View</div>
</div>

<div class="abs card" style="left:391px;top:931px">
  <div class="art" style="left:27px;top:0;width:156px;height:40px;background:#f6d21a" role="img" aria-label="Yellow hang-out birthday invitation"></div>
</div>
<div class="abs card" style="left:619px;top:931px">
  <div class="art" style="left:0;top:0;width:209px;height:40px;background:#f7e4a6" role="img" aria-label="Cream toy themed birthday invitation"></div>
</div>
<div class="abs card" style="left:846px;top:931px">
  <div class="art" style="left:0;top:0;width:209px;height:40px;background:linear-gradient(90deg,#7fbe3c,#f0a030)" role="img" aria-label="Guitar rock birthday invitation"></div>
</div>

</body>
</html>
```